Business card design for Brivo Engineering Tandem

We need a new business card design along with all the necessary to place an order. The company is Brivo Engineering Tandem and we recently updated our logo.

```html
<!DOCTYPE html>
<html lang="en">
<head>
<meta charset="utf-8">
<title>Brivo Engineering Tandem – Business Card</title>
<link href="https://fonts.googleapis.com/css2?family=Poppins:wght@400;500;600;700&display=swap" rel="stylesheet">
<style>
  :root {
    --page-bg: #e4e4e4;
    --card-white: #f7f7f5;
    --brand-yellow: #dfbd25;
    --brand-grey: #8f8f8f;
    --ink: #1d1d1d;
    --shadow: rgba(0,0,0,0.14);
  }
  * { box-sizing: border-box; margin: 0; padding: 0; }
  html, body { width: 1200px; height: 930px; overflow: hidden; }
  body {
    background: var(--page-bg);
    font-family: "Poppins", sans-serif;
    position: relative;
  }
  .card {
    position: absolute;
    width: 640px;
    height: 366px;
    box-shadow: 0 10px 24px var(--shadow);
  }
  .card--back {
    left: 500px; top: 90px;
    background: var(--brand-yellow);
    display: flex; align-items: center; justify-content: center;
  }
  .card--front {
    left: 60px; top: 480px;
    background: var(--card-white);
    padding: 44px 40px 0;
    text-align: center;
  }
  .brand { display: inline-flex; align-items: center; gap: 14px; }
  .brand__mark { width: 18px; height: 18px; }
  .brand__name {
    color: var(--brand-grey);
    font-weight: 600;
    letter-spacing: 1px;
    text-transform: uppercase;
    line-height: 1.15;
  }
  .card--back .brand__mark { background: #ffffff; width: 26px; height: 26px; }
  .card--back .brand__name { font-size: 36px; text-align: left; }
  .card--front .brand__mark { background: var(--brand-yellow); }
  .card--front .brand__name { font-size: 24px; text-align: left; }
  .holder { margin-top: 26px; }
  .holder__name {
    font-size: 20px; font-weight: 700; color: #6e6e6e;
    letter-spacing: 1px; text-transform: uppercase;
  }
  .holder__role {
    font-size: 13px; color: var(--brand-yellow);
    letter-spacing: 1px; text-transform: uppercase;
  }
  .details {
    margin-top: 26px;
    display: flex; justify-content: center; align-items: stretch; gap: 18px;
    color: var(--ink); font-size: 15px; line-height: 1.55;
  }
  .details__address { text-align: right; }
  .details__divider { width: 1px; background: #555; }
  .details__contacts { text-align: left; list-style: none; }
  .details__contacts li { display: flex; align-items: center; gap: 8px; }
  .icon { width: 13px; height: 13px; fill: var(--brand-yellow); flex: none; }
</style>
</head>
<body>
  <section class="card card--back" aria-label="Card back">
    <div class="brand">
      <span class="brand__mark"></span>
      <span class="brand__name">Brivo Engineering<br>Tandem</span>
    </div>
  </section>

  <section class="card card--front" aria-label="Card front">
    <div class="brand">
      <span class="brand__mark"></span>
      <span class="brand__name">Brivo Engineering<br>Tandem</span>
    </div>
    <div class="holder">
      <p class="holder__name">Marcus Hale</p>
      <p class="holder__role">Managing Director</p>
    </div>
    <div class="details">
      <address class="details__address" style="font-style:normal">
        58, Harlow Street<br>Unit 4<br>30917, Eastland
      </address>
      <span class="details__divider"></span>
      <ul class="details__contacts">
        <li><svg class="icon" viewBox="0 0 24 24"><path d="M6.6 10.8a15.1 15.1 0 0 0 6.6 6.6l2.2-2.2a1 1 0 0 1 1-.25 11.4 11.4 0 0 0 3.6.57 1 1 0 0 1 1 1V20a1 1 0 0 1-1 1A17 17 0 0 1 3 4a1 1 0 0 1 1-1h3.5a1 1 0 0 1 1 1c0 1.25.2 2.45.57 3.57a1 1 0 0 1-.25 1z"/></svg>044-987 650 312</li>
        <li><svg class="icon" viewBox="0 0 24 24"><path d="M2 5h20v14H2z M2 5l10 8 10-8" fill="none" stroke="#dfbd25" stroke-width="2.4"/></svg>info@brivotandem.com</li>
        <li><svg class="icon" viewBox="0 0 24 24"><circle cx="12" cy="12" r="10"/><path d="M2 12h20M12 2c3 3 3 17 0 20M12 2c-3 3-3 17 0 20" stroke="#f7f7f5" stroke-width="1.6" fill="none"/></svg>www.brivotandem.com</li>
      </ul>
    </div>
  </section>
</body>
</html>
```